Meridale Real Estate

We are looking for help with web design for a new company that is revolutionizing the real estate world on the listing side: by charing per hour for top level professional real estate services. We would like the concept to be simple, clean and easily understood.
Updates

We want this website to actually function, not just a static design.

Industry/Entity Type

Real Estate

```html
<!DOCTYPE html>
<html lang="en">
<head>
<meta charset="utf-8">
<title>Meridale Real Estate</title>
<link rel="stylesheet" href="https://fonts.googleapis.com/css2?family=Roboto+Condensed:wght@400;700&family=Roboto:wght@400&display=swap">
<style>
  :root {
    --night: #0d1522;
    --night-deep: #05080d;
    --white: #ffffff;
    --sky-blue: #1ea3e0;
    --panel-grey: #454545;
    --footer: #1c1c1c;
    --footer-text: #a9a9a9;
    --arrow-bg: rgba(120,120,120,0.55);
    --social: #6c6c6c;
  }
  * { margin: 0; padding: 0; box-sizing: border-box; }
  html, body { width: 1200px; height: 816px; overflow: hidden; background: var(--night-deep); }
  body { position: relative; font-family: "Roboto Condensed", Arial, sans-serif; color: var(--white); }

  .hero-photo {
    position: absolute; left: 0; top: 0; width: 1200px; height: 740px;
    background:
      radial-gradient(ellipse 420px 240px at 600px 330px, rgba(230,215,180,0.55), transparent 70%),
      linear-gradient(180deg, #0b1626 0%, #1d3350 28%, #3a4a55 45%, #2d3a2a 62%, #15201a 80%, #0a0e10 100%);
  }

  .brand {
    position: absolute; left: 190px; top: 24px; width: 140px; height: 120px;
    display: flex; align-items: center; gap: 10px;
  }
  .brand-dot { width: 14px; height: 14px; border: 2px solid var(--white); border-radius: 50%; flex: none; }
  .brand-name { font-size: 17px; font-weight: 400; letter-spacing: 2px; line-height: 1.3; text-transform: uppercase; color: var(--white); }

  .search {
    position: absolute; left: 807px; top: 19px; width: 216px; height: 25px;
    background: var(--white); border-radius: 3px; display: flex; align-items: center; padding: 0 10px;
    font-family: "Roboto", Arial, sans-serif; font-size: 11px; color: #888;
  }
  .search svg { position: absolute; right: 8px; top: 6px; }

  .main-nav { position: absolute; top: 76px; left: 0; }
  .main-nav a {
    position: absolute; font-size: 15px; font-weight: 700; color: var(--white);
    text-decoration: none; white-space: nowrap; text-transform: uppercase;
  }
  .main-nav .active::before {
    content: ""; position: absolute; left: -12px; right: -12px; top: -18px; height: 2px; background: var(--sky-blue);
  }

  .headline {
    position: absolute; left: 176px; top: 462px; width: 520px;
    font-size: 27px; font-weight: 400; line-height: 40px; text-transform: uppercase;
  }

  .slider-arrows { position: absolute; left: 937px; top: 497px; display: flex; gap: 3px; }
  .slider-arrows span { width: 40px; height: 41px; background: var(--arrow-bg); display: flex; align-items: center; justify-content: center; }

  .feature { position: absolute; top: 549px; width: 410px; height: 172px; display: flex; }
  .feature-photo { width: 206px; height: 172px; }
  .feature-body { flex: 1; padding: 30px 16px 0; text-align: center; }
  .feature-title { font-family: "Roboto", Arial, sans-serif; font-size: 13px; letter-spacing: 2px; text-transform: uppercase; margin-bottom: 14px; }
  .feature-text { font-family: "Roboto", Arial, sans-serif; font-size: 11px; line-height: 20px; }
  .feature--homes { left: 181px; }
  .feature--homes .feature-photo { background: linear-gradient(160deg, #1b3a78 0%, #3b5d95 45%, #d8d2c4 70%, #3a3a38 100%); }
  .feature--homes .feature-body { background: var(--sky-blue); }
  .feature--offices { left: 611px; }
  .feature--offices .feature-photo { background: linear-gradient(170deg, #2f6fc7 0%, #7fa6d8 40%, #c9cfd4 65%, #5e8a4c 100%); }
  .feature--offices .feature-body { background: var(--panel-grey); }

  .site-footer { position: absolute; left: 0; top: 740px; width: 1200px; height: 76px; background: var(--footer); }
  .footer-nav { position: absolute; left: 187px; top: 19px; display: flex; gap: 24px; }
  .footer-nav a { font-family: "Roboto", Arial, sans-serif; font-size: 10.5px; color: var(--footer-text); text-decoration: none; text-transform: uppercase; }
  .copyright { position: absolute; left: 187px; top: 48px; font-family: "Roboto", Arial, sans-serif; font-size: 8px; color: var(--white); }
  .social { position: absolute; left: 918px; top: 25px; display: flex; gap: 5px; }
  .social span { width: 22px; height: 22px; border-radius: 50%; background: var(--social); }
</style>
</head>
<body>
  <div class="hero-photo" role="img" aria-label="Luxury colonial-style mansion with palm trees, lit at dusk"></div>

  <header>
    <div class="brand">
      <span class="brand-dot"></span>
      <span class="brand-name">Meridale<br>Real Estate</span>
    </div>
    <div class="search">Search :
      <svg width="13" height="13" viewBox="0 0 13 13"><circle cx="5" cy="5" r="4" fill="none" stroke="#aaa" stroke-width="1.5"/><line x1="8" y1="8" x2="12" y2="12" stroke="#aaa" stroke-width="1.5"/></svg>
    </div>
    <nav class="main-nav">
      <a class="active" style="left:467px">Home</a>
      <a style="left:539px">Commercial</a>
      <a style="left:651px">Residential</a>
      <a style="left:759px">Farm</a>
      <a style="left:828px">Vacant Land</a>
      <a style="left:941px">Contact</a>
    </nav>
  </header>

  <h1 class="headline">We sell luxury homes, office buildings, farms, and ranches.</h1>

  <div class="slider-arrows">
    <span><svg width="10" height="18" viewBox="0 0 10 18"><polyline points="9,1 1,9 9,17" fill="none" stroke="#fff" stroke-width="1.5"/></svg></span>
    <span><svg width="10" height="18" viewBox="0 0 10 18"><polyline points="1,1 9,9 1,17" fill="none" stroke="#fff" stroke-width="1.5"/></svg></span>
  </div>

  <section class="feature feature--homes">
    <div class="feature-photo" role="img" aria-label="Modern white luxury home at dusk"></div>
    <div class="feature-body">
      <h2 class="feature-title">Luxury Homes</h2>
      <p class="feature-text">uncover many web sites still in their infancy. Various versions have evolved over the years, sometimes by accident...</p>
    </div>
  </section>

  <section class="feature feature--offices">
    <div class="feature-photo" role="img" aria-label="Modern glass office building under blue sky"></div>
    <div class="feature-body">
      <h2 class="feature-title">Office Buildings</h2>
      <p class="feature-text">uncover many web sites still in their infancy. Various versions have evolved over the years, sometimes by accident...</p>
    </div>
  </section>

  <footer class="site-footer">
    <nav class="footer-nav">
      <a>Home</a><a>Commercial</a><a>Residential</a><a>Farm</a><a>Vacant Land</a><a>Contact</a>
    </nav>
    <p class="copyright">© Copyrights 2015 Meridale Real Estate. All Right Reserved</p>
    <div class="social" aria-label="Social links"><span></span><span></span><span></span><span></span></div>
  </footer>
</body>
</html>
```